Business Card Design

IT Solutions company.

I need a professional looking design with my company logo if possible.

Logo is located here:
http://www.brunelwavesystems.co.uk/dev/images/logo1.jpg
Feel free to redesign the logo if you think you have any better suggestions.

Our services include, IT Infrastructure/Telephony Maintenance & Hosting Services. Linux and Windows Solutions, App Development.

Out website is currently under development:
http://www.brunelwavesystems.co.uk/dev/

I'm looking for a colourful but professional looking business card.

Industry/Entity Type

Business

Contact Information for Business Card

BW Brunel Wavesystems Ltd
Martin Hollisby
07700958312
www.brunelwavesystems.co.uk
mhollisby@brunelwavesystems.co.uk

```html
<!DOCTYPE html>
<html lang="en">
<head>
<meta charset="utf-8">
<title>BW Brunel Wavesystems Ltd – Business Card</title>
<link rel="stylesheet" href="https://fonts.googleapis.com/css2?family=Oswald:wght@500&family=Roboto:wght@400;700&family=Roboto+Condensed:wght@700&display=swap">
<style>
  :root {
    --stage: #1c1d1f;
    --card-white: #ffffff;
    --card-grey-top: #fbfbfb;
    --card-grey-bottom: #e6e7e8;
    --brand-blue: #1f4fa8;
    --ink-dark: #2b2b2d;
    --ink-mid: #4a4a4d;
    --band-dark: #3a3a3c;
    --band-text: #f2f2f2;
  }
  * { box-sizing: border-box; margin: 0; padding: 0; }
  html, body {
    width: 1200px; height: 864px; overflow: hidden;
    background: var(--stage);
  }
  .canvas { position: relative; width: 1200px; height: 864px; }

  .card {
    position: absolute; width: 520px; height: 297px;
    border-radius: 3px; overflow: hidden;
    box-shadow: 0 14px 30px rgba(0,0,0,.45);
  }
  .card--front { left: 60px; top: 130px; background: var(--card-white); }
  .card--back {
    left: 620px; top: 437px;
    background: linear-gradient(180deg, var(--card-grey-top), var(--card-grey-bottom));
  }

  .wordmark {
    position: absolute; display: flex; align-items: center; gap: 10px;
    font-family: "Roboto Condensed", "Arial Narrow", sans-serif;
    font-weight: 700; color: var(--ink-dark); white-space: nowrap;
  }
  .wordmark__dot { border-radius: 50%; background: var(--brand-blue); flex: none; }
  .card--front .wordmark { left: 40px; top: 118px; font-size: 30px; }
  .card--front .wordmark__dot { width: 46px; height: 46px; }
  .card--back .wordmark { right: 28px; top: 98px; font-size: 21px; }
  .card--back .wordmark__dot { width: 32px; height: 32px; }

  .card__bands { position: absolute; left: 0; top: 0; width: 520px; height: 297px; }

  .holder { position: absolute; left: 26px; top: 150px; }
  .holder__name {
    font-family: "Oswald", "Arial Narrow", sans-serif; font-weight: 500;
    font-size: 20px; letter-spacing: .5px; color: var(--ink-dark); line-height: 1;
  }
  .holder__role {
    font-family: "Roboto", Arial, sans-serif; font-size: 9px; letter-spacing: 1.2px;
    color: var(--ink-mid); margin-top: 4px;
  }

  .contacts {
    position: absolute; left: 26px; top: 204px; list-style: none;
    font-family: "Roboto", Arial, sans-serif; font-size: 9.5px; color: var(--ink-mid);
  }
  .contacts__item { display: flex; align-items: center; gap: 7px; height: 17px; }
  .contacts__icon { width: 10px; height: 10px; fill: var(--ink-mid); flex: none; }

  .address {
    position: absolute; right: 26px; top: 222px;
    font-family: "Roboto", Arial, sans-serif; font-size: 12px; letter-spacing: .6px;
    color: var(--band-text);
  }
</style>
</head>
<body>
<main class="canvas">

  <section class="card card--front" aria-label="Card front">
    <div class="wordmark">
      <span class="wordmark__dot"></span>
      <span class="wordmark__name">BW Brunel Wavesystems Ltd</span>
    </div>
  </section>

  <section class="card card--back" aria-label="Card back">
    <svg class="card__bands" viewBox="0 0 520 297" aria-hidden="true">
      <path fill="var(--brand-blue)" d="M0 278 H214 C236 278 232 192 258 192 H520 V297 H0 Z"/>
      <path fill="var(--band-dark)" d="M0 284 H219 C241 284 238 199 263 199 H520 V297 H0 Z"/>
    </svg>

    <div class="wordmark">
      <span class="wordmark__dot"></span>
      <span class="wordmark__name">BW Brunel Wavesystems Ltd</span>
    </div>

    <div class="holder">
      <p class="holder__name">MARTIN HOLLISBY</p>
      <p class="holder__role">GENERAL MANAGER</p>
    </div>

    <ul class="contacts">
      <li class="contacts__item">
        <svg class="contacts__icon" viewBox="0 0 10 10"><path d="M2.2 0.6 L3.8 2.6 L2.9 3.7 C3.5 5 4.9 6.4 6.3 7.1 L7.4 6.2 L9.4 7.8 L8.5 9.4 C4.5 9.2 0.8 5.5 0.6 1.5 Z"/></svg>
        <span>07700958312</span>
      </li>
      <li class="contacts__item">
        <svg class="contacts__icon" viewBox="0 0 10 10"><path d="M0.5 2 H9.5 V8.5 H0.5 Z M1.2 2.6 L5 5.6 L8.8 2.6 V3.4 L5 6.4 L1.2 3.4 Z" fill-rule="evenodd"/></svg>
        <span>mhollisby@brunelwavesystems.co.uk</span>
      </li>
      <li class="contacts__item">
        <svg class="contacts__icon" viewBox="0 0 10 10"><path fill-rule="evenodd" d="M5 0.4 A4.6 4.6 0 1 1 4.99 0.4 Z M5 1.3 A3.7 3.7 0 1 0 5.01 1.3 Z M4.6 1 H5.4 V9 H4.6 Z M1 4.6 H9 V5.4 H1 Z"/></svg>
        <span>www.brunelwavesystems.co.uk</span>
      </li>
    </ul>

    <p class="address">12 Harbour Lane, Unit 3, Bristol</p>
  </section>

</main>
</body>
</html>
```